Veltrane Group Business Card Design

The CEO is looking for a new trendy look for his business card.
You can stay with current branding or come up with something new/creative. It can be 3D, including Medical Office buildings. You can use our logo in a variety of colors. Please include name, title, company name, company website, email address, cell number

Target Market(s)

Real Estate Development and Construction

Industry/Entity Type

Health care real estate

Contact Information for Business Card

Rohesh Kamdar, CEO M-604.781.2249 E-roheshkamdar@veltrane.com Address:4180 Lindqvist Ave, Tampa, FL 33482 www.veltrane.com

Font styles to use
Other font styles liked:
• Be creative

Requirements
Must have
• Creative, trendy look
Nice to have
• Please go to our website to get a feel- www. veltrane.com
Should not have
• small fonts

```html
<!DOCTYPE html>
<html lang="en">
<head>
<meta charset="utf-8">
<title>Veltrane Group Business Card</title>
<link href="https://fonts.googleapis.com/css2?family=Open+Sans:wght@400;700;800&display=swap" rel="stylesheet">
<style>
  :root {
    --stage: #2b2d31;
    --ink: #0d0d0d;
    --paper: #ffffff;
    --emboss: #1b1b1b;
    --muted: #d8d8d8;
  }
  * { box-sizing: border-box; margin: 0; padding: 0; }
  html, body { width: 1200px; height: 900px; overflow: hidden; }
  body {
    background: var(--stage);
    font-family: "Open Sans", Arial, sans-serif;
    display: flex;
    flex-direction: column;
    align-items: center;
    justify-content: center;
    gap: 40px;
  }
  .card {
    position: relative;
    width: 700px;
    height: 400px;
    border-radius: 28px;
    overflow: hidden;
  }
  .card--front { background: var(--paper); }
  .card--back { background: var(--ink); display: flex; align-items: center; justify-content: center; }
  .card__wave { position: absolute; inset: 0; width: 100%; height: 100%; }
  .holder { position: absolute; left: 42px; top: 38px; color: var(--ink); }
  .holder__name { font-size: 26px; font-weight: 700; line-height: 1.1; }
  .holder__title { font-size: 15px; font-weight: 400; margin-top: 4px; }
  .contact {
    position: absolute; left: 42px; top: 212px;
    color: var(--paper); font-size: 15px; line-height: 1.45; list-style: none;
  }
  .contact__address { margin-bottom: 8px; }
  .contact__item { display: flex; align-items: center; gap: 10px; }
  .contact__icon { width: 13px; height: 13px; fill: var(--paper); flex: none; }
  .brand {
    position: absolute; right: 40px; top: 130px;
    text-align: right; color: var(--ink); font-weight: 800; line-height: 0.95;
  }
  .brand__name { font-size: 66px; letter-spacing: -2px; }
  .brand__group { font-size: 32px; }
  .brand--back { position: static; color: var(--emboss); }
  .brand--back .brand__name { font-size: 96px; }
  .brand--back .brand__group { font-size: 46px; }
</style>
</head>
<body>
  <section class="card card--front">
    <svg class="card__wave" viewBox="0 0 700 400" aria-hidden="true">
      <path d="M0,118 C180,96 300,160 380,252 C450,330 560,306 700,270" fill="none" stroke="#0d0d0d" stroke-width="7"/>
      <path d="M0,150 C180,130 300,190 380,280 C450,355 560,332 700,300 L700,400 L0,400 Z" fill="#0d0d0d"/>
    </svg>

    <header class="holder">
      <h1 class="holder__name">Rohesh Kamdar</h1>
      <p class="holder__title">CEO</p>
    </header>

    <div class="brand">
      <div class="brand__name">Veltrane</div>
      <div class="brand__group">Group</div>
    </div>

    <ul class="contact">
      <li class="contact__address">4180 Lindqvist Ave,<br>Tampa, FL 33482</li>
      <li class="contact__item">
        <svg class="contact__icon" viewBox="0 0 24 24"><path d="M6.6 10.8a15.1 15.1 0 0 0 6.6 6.6l2.2-2.2c.3-.3.7-.4 1-.2 1.1.4 2.3.6 3.6.6.6 0 1 .4 1 1V20c0 .6-.4 1-1 1A17 17 0 0 1 3 4c0-.6.4-1 1-1h3.5c.6 0 1 .4 1 1 0 1.3.2 2.5.6 3.6.1.3 0 .7-.2 1z"/></svg>
        604.781.2249
      </li>
      <li class="contact__item">
        <svg class="contact__icon" viewBox="0 0 24 24"><path d="M2 5h20v14H2z M3 6l9 7 9-7" fill="none" stroke="#fff" stroke-width="2"/></svg>
        roheshkamdar@veltrane.com
      </li>
      <li class="contact__item">
        <svg class="contact__icon" viewBox="0 0 24 24"><circle cx="12" cy="12" r="9" fill="none" stroke="#fff" stroke-width="2"/><path d="M3 12h18M12 3c3 3 3 15 0 18M12 3c-3 3-3 15 0 18" fill="none" stroke="#fff" stroke-width="1.5"/></svg>
        www.veltrane.com
      </li>
    </ul>
  </section>

  <section class="card card--back">
    <div class="brand brand--back">
      <div class="brand__name">Veltrane</div>
      <div class="brand__group">Group</div>
    </div>
  </section>
</body>
</html>
```